i would like a business card to leave with customers and potential customers for electrical work and for the supply and install of reverse cycle airconditioning in the domestic and commercial market.
I own my own business and im a sole trader. I have an a'class electrical lisence and also a refrigeration lisence so i am
able to offer complete installations in airconditioning by a fully qualified and lisenced tradesman.
im looking for something that comes across as unique and professional.
i had the coluor black and some gold in mind but open to any coluors.
something like Lanterra Electrical & Refrigeration
or Lanterra Air.
i will use this design on a business card to advertise through summer to help generate installs through the busy season.

Target Market(s)

Mainly domestic house holds through summer who are in need of airconditioning and reliable information to acomadate thier cooling and heating requirements

Industry/Entity Type

Electrical

Requirements
Must have
• Business name- Lanterra
My name- Mark Delford
My mobile no- 0438 517 290
My email- mrdelford@qelvo.com.au
Installation & Decomissioning of aiconditioning split systems
LIC NO: TRK 540316
Nice to have
• Lanterra Electrical & Refrigeration

```html
<!DOCTYPE html>
<html lang="en">
<head>
<meta charset="utf-8">
<title>Lanterra Electrical &amp; Refrigeration – Business Card</title>
<link rel="stylesheet" href="https://fonts.googleapis.com/css2?family=EB+Garamond:wght@400;500&family=Cabin:wght@400&display=swap">
<style>
  :root {
    --backdrop: #3d4a49;
    --card-top: #3a3a3c;
    --card-bottom: #1c1c1e;
    --brand-red: #e0302a;
    --brand-red-light: #f05a4a;
    --brand-red-dark: #a81a16;
    --name-grey: #cfcfcf;
    --label-grey: #9c9c9c;
    --value-grey: #d6d6d6;
    --footer-text: #e4e4e4;
    --badge-tile: #e8e8e8;
  }
  * { box-sizing: border-box; margin: 0; padding: 0; }
  html, body {
    width: 1200px; height: 750px; overflow: hidden;
    background: var(--backdrop);
  }
  .stage { position: relative; width: 1200px; height: 750px; }

  .card {
    position: absolute; top: 241px; width: 544px; height: 333px;
    background: radial-gradient(ellipse at 50% 30%, var(--card-top), var(--card-bottom) 85%);
    box-shadow: 0 6px 18px rgba(0,0,0,.45);
    overflow: hidden;
    font-family: "EB Garamond", Georgia, serif;
  }
  .card--front { left: 33px; }
  .card--back { left: 617px; }

  .swoosh { position: absolute; inset: 0; width: 544px; height: 333px; }

  .brand {
    position: absolute; left: 28px; top: 20px;
    font-family: "EB Garamond", Georgia, serif;
    font-weight: 400; color: var(--brand-red);
    font-size: 44px; line-height: 1;
  }
  .brand__sub { display: block; font-size: 24px; margin-left: 118px; margin-top: 2px; letter-spacing: 2px; }

  .owner-name {
    position: absolute; right: 34px; top: 103px;
    font-size: 35px; font-weight: 400; color: var(--name-grey);
  }

  .contact { position: absolute; left: 28px; top: 159px; list-style: none; }
  .contact li { font-size: 19px; line-height: 24.5px; color: var(--label-grey); }
  .contact .value { color: var(--value-grey); }

  .services {
    position: absolute; left: 35px; bottom: 12px;
    font-size: 18px; color: var(--footer-text);
  }

  .badge { position: absolute; left: 481px; top: 270px; width: 45px; height: 50px; }

  .back-brand {
    position: absolute; left: 0; right: 0; top: 118px; text-align: center;
    font-size: 72px; font-weight: 400; color: var(--brand-red); line-height: 1;
  }
  .back-tagline {
    position: absolute; left: 0; right: 0; bottom: 19px; text-align: center;
    font-family: "Cabin", Arial, sans-serif;
    font-size: 20px; letter-spacing: 5.5px; color: var(--brand-red);
  }
</style>
</head>
<body>
<main class="stage">
  <section class="card card--front" aria-label="Business card front">
    <svg class="swoosh" viewBox="0 0 544 333" aria-hidden="true">
      <defs>
        <linearGradient id="swooshFill" x1="0" y1="0" x2="1" y2="0">
          <stop offset="0" stop-color="var(--brand-red-dark)"/>
          <stop offset=".6" stop-color="var(--brand-red)"/>
          <stop offset="1" stop-color="var(--brand-red-light)"/>
        </linearGradient>
        <linearGradient id="baseFill" x1="0" y1="0" x2="0" y2="1">
          <stop offset="0" stop-color="#2a2a2c"/>
          <stop offset="1" stop-color="#0e0e0f"/>
        </linearGradient>
      </defs>
      <path d="M0,268 C210,292 430,270 544,180 L544,333 L0,333 Z" fill="url(#baseFill)"/>
      <path d="M0,263 C220,288 420,262 544,158 L544,182 C430,270 215,292 0,270 Z" fill="url(#swooshFill)"/>
    </svg>

    <div class="brand">Lanterra<span class="brand__sub">Electrical</span></div>
    <h1 class="owner-name">Mark Delford</h1>
    <ul class="contact">
      <li>mob:&nbsp; <span class="value">0438 517 290</span></li>
      <li>email: <span class="value">mrdelford@qelvo.com.au</span></li>
      <li>LIC No: <span class="value">TRK 540316</span></li>
      <li>LIC No: <span class="value">L318904</span></li>
    </ul>
    <p class="services">Installation &amp; Decomissioning of airconditioning Split Systems</p>

    <svg class="badge" viewBox="0 0 45 50" role="img" aria-label="Installer certification badge">
      <rect width="45" height="50" fill="var(--badge-tile)"/>
    </svg>
  </section>

  <section class="card card--back" aria-label="Business card back">
    <div class="back-brand">Lanterra</div>
    <p class="back-tagline">Lanterra Electrical &amp; Refrigeration</p>
  </section>
</main>
</body>
</html>
```